A picture window of stained glass as seen in older churches,
Etched in it is the tree of life.
God lead ministry

Industry/Entity Type

Ministry

Contact Information for Business Card

Bright Meadow/River Stone. Ministries
Lena Marwick, Founder
P.O. Box 20487 Colorado Springs, CO 80915-2487
719-286-4172

Font styles to use
Sans Serif

```html
<!DOCTYPE html>
<html lang="en">
<head>
<meta charset="utf-8">
<title>Bright Meadow – Business Card</title>
<link rel="stylesheet" href="https://fonts.googleapis.com/css2?family=Lato:wght@400;700;900&display=swap">
<style>
  :root {
    --page-bg: #6e6e6e;
    --card-bg: #0b0b0b;
    --title-grey: #b9b9b9;
    --text-grey: #8c8c8c;
    --brand-green: #3fae49;
    --band-green: #0f9a48;
    --swoosh-green: #7dc242;
    --white: #ffffff;
  }
  * { margin: 0; padding: 0; box-sizing: border-box; }
  html, body {
    width: 1200px; height: 900px; overflow: hidden;
    background: var(--page-bg);
    font-family: "Lato", Arial, sans-serif;
  }
  .card {
    position: absolute; left: 75px; top: 150px;
    width: 1050px; height: 600px;
    background: var(--card-bg);
    overflow: hidden;
  }
  .card-art { position: absolute; inset: 0; }
  .identity { position: absolute; left: 500px; top: 110px; }
  .ministry-name {
    font-weight: 900; font-size: 50px; letter-spacing: 1px;
    color: var(--title-grey); text-transform: uppercase; line-height: 1;
  }
  .ministry-sub {
    font-size: 31px; color: var(--brand-green); margin-top: 8px; letter-spacing: 0.5px;
  }
  .person { position: absolute; left: 500px; top: 272px; }
  .person-name { font-size: 46px; color: var(--brand-green); line-height: 1; }
  .person-name strong { font-weight: 700; }
  .person-role {
    font-weight: 700; font-size: 22px; letter-spacing: 5px; line-height: 1;
    color: var(--brand-green); margin-top: 14px; text-transform: uppercase;
  }
  .phone {
    display: flex; align-items: center; gap: 12px; line-height: 1;
    margin-top: 22px; font-size: 28px; color: var(--text-grey);
  }
  .phone svg { width: 28px; height: 28px; }
  .address {
    position: absolute; left: 300px; top: 524px;
    display: flex; align-items: center; gap: 18px;
    font-weight: 700; font-size: 25px; color: var(--white);
    letter-spacing: 0.8px; text-transform: uppercase;
  }
  .address svg { width: 24px; height: 32px; }
</style>
</head>
<body>
  <div class="card">
    <svg class="card-art" viewBox="0 0 1050 600" width="1050" height="600">
      <defs>
        <linearGradient id="window-glass" x1="0" y1="0" x2="0" y2="1">
          <stop offset="0" stop-color="#9fc4e6"/>
          <stop offset="0.35" stop-color="#5f88b8"/>
          <stop offset="0.6" stop-color="#c9a23a"/>
          <stop offset="1" stop-color="#6b5a2e"/>
        </linearGradient>
      </defs>
      <path class="window-frame" d="M175,468 L175,150 A72,72 0 0 1 319,150 L319,468 Z" fill="#1c2a26"/>
      <path class="window-glass" role="img" aria-label="Stained glass church window with a robed figure"
            d="M189,454 L189,152 A58,58 0 0 1 305,152 L305,454 Z" fill="url(#window-glass)"/>
      <path class="swoosh-accent" d="M0,522 C200,490 450,464 700,454 C450,474 220,508 0,554 Z" fill="var(--swoosh-green)"/>
      <path class="address-band" d="M0,572 C300,508 650,440 1050,408 L1050,600 L0,600 Z" fill="var(--band-green)"/>
    </svg>

    <div class="identity">
      <h1 class="ministry-name">Bright Meadow</h1>
      <p class="ministry-sub">River Stone. Ministries</p>
    </div>

    <div class="person">
      <p class="person-name">Lena <strong>Marwick</strong></p>
      <p class="person-role">Founder</p>
      <p class="phone">
        <svg viewBox="0 0 24 24" aria-hidden="true"><path fill="var(--brand-green)" d="M3,9 C3,6 7,5 12,5 C17,5 21,6 21,9 L21,11 L17,11 L16,8.5 C13,8 11,8 8,8.5 L7,11 L3,11 Z M6,12 L18,12 L20,20 L4,20 Z"/><circle cx="12" cy="16" r="2.2" fill="var(--card-bg)"/></svg>
        <span>719-286-4172</span>
      </p>
    </div>

    <p class="address">
      <svg viewBox="0 0 24 32" aria-hidden="true"><path fill="var(--white)" d="M12,0 C5.4,0 0,5.2 0,11.7 C0,20 12,32 12,32 C12,32 24,20 24,11.7 C24,5.2 18.6,0 12,0 Z"/><circle cx="12" cy="11.5" r="4.5" fill="var(--band-green)"/></svg>
      <span>P.O. Box 20487 Colorado Springs, CO 80915-2487</span>
    </p>
  </div>
</body>
</html>
```